Freelance business trainer needs a new business card

My business is called Brontlearn. I provide training in the workplace on management, coaching and mentoring, and customer service topics for a variety of businesses, colleges and private training providers, and teach on management programs. I need a professional but eye catching business card. Business colours grey and orange. My name Marion Tadwick; Tel 07382 415067; email mtadwick@brontlearn.co.uk; website www.brontlearn.co.uk.
Happy to have some sort of logo on front and details on back or all on one side
Target Market(s)
SME businesses and colleges - workshops i run are for adults in the workplace
Industry/Entity Type
Training
Look and feel

```html
<!DOCTYPE html>
<html lang="en">
<head>
<meta charset="utf-8">
<title>Brontlearn business card</title>
<link rel="stylesheet" href="https://fonts.googleapis.com/css2?family=Open+Sans:wght@400;600;700&display=swap">
<style>
  :root {
    --backdrop: #c3d0d9;
    --charcoal: #404040;
    --orange: #f49020;
    --white: #ffffff;
    --tint: #f6f3ef;
  }
  * { box-sizing: border-box; margin: 0; padding: 0; }
  html, body {
    width: 1200px; height: 965px; overflow: hidden;
    background: var(--backdrop);
    font-family: "Open Sans", sans-serif;
  }
  .card {
    position: absolute; left: 265px; width: 663px; height: 380px;
    border-radius: 22px; overflow: hidden;
  }
  .card-front { top: 77px; background: var(--charcoal); }
  .card-back { top: 521px; background: var(--white); }

  .brand {
    position: absolute; display: flex; align-items: center;
    color: var(--orange); font-weight: 600; letter-spacing: 0.5px;
  }
  .brand-mark { background: var(--orange); flex: none; }
  .card-front .brand {
    left: 0; right: 0; top: 0; bottom: 0; justify-content: center;
    font-size: 78px; gap: 22px;
  }
  .card-front .brand-mark { width: 56px; height: 56px; }
  .card-back .brand {
    left: 60px; top: 88px; font-size: 44px; gap: 14px;
  }
  .card-back .brand-mark { width: 30px; height: 30px; }

  .back-tint {
    position: absolute; right: 0; top: 0; width: 170px; height: 220px;
    background: linear-gradient(180deg, var(--tint), rgba(246,243,239,0));
  }
  .back-band { position: absolute; left: 0; top: 0; width: 663px; height: 380px; }

  .holder {
    position: absolute; right: 36px; top: 224px; text-align: right;
    font-size: 18px; line-height: 22px;
  }
  .holder-name { color: var(--charcoal); font-weight: 700; }
  .holder-role { color: var(--white); }

  .contact-list {
    position: absolute; left: 38px; top: 264px; list-style: none;
    color: var(--orange); font-size: 18px; line-height: 28.5px;
  }
  .contact-list li { display: flex; align-items: center; gap: 7px; }
  .contact-list svg { width: 17px; height: 17px; flex: none; }
</style>
</head>
<body>
  <section class="card card-front">
    <div class="brand"><span class="brand-mark"></span>Brontlearn</div>
  </section>

  <section class="card card-back">
    <div class="back-tint"></div>
    <div class="brand"><span class="brand-mark"></span>Brontlearn</div>

    <svg class="back-band" viewBox="0 0 663 380" aria-hidden="true">
      <polygon points="0,229 663,229 663,380 0,380" fill="var(--charcoal)"/>
      <polygon points="0,220 400,220 441,271 663,271 663,220 663,229 0,229" fill="var(--orange)"/>
      <polygon points="400,220 663,220 663,271 441,271" fill="var(--orange)"/>
    </svg>

    <div class="holder">
      <p class="holder-name">Marion Tadwick</p>
      <p class="holder-role">Owner</p>
    </div>

    <ul class="contact-list">
      <li>
        <svg viewBox="0 0 20 20" aria-hidden="true"><path fill="#fff" d="M2 7c0-3 3-4 8-4s8 1 8 4v1h-4V6H6v2H2zM5 9h10l2 8H3zM10 11a2 2 0 1 0 0 4 2 2 0 0 0 0-4z"/></svg>
        07382 415067
      </li>
      <li>
        <svg viewBox="0 0 20 20" aria-hidden="true"><rect x="2" y="4" width="16" height="12" fill="#fff"/><path d="M2 4l8 7 8-7" fill="none" stroke="var(--charcoal)" stroke-width="1.5"/></svg>
        mtadwick@brontlearn.co.uk
      </li>
      <li>
        <svg viewBox="0 0 20 20" aria-hidden="true" fill="none" stroke="#fff" stroke-width="1.5"><circle cx="10" cy="10" r="8"/><ellipse cx="10" cy="10" rx="3.5" ry="8"/><path d="M2 10h16M3.5 6h13M3.5 14h13"/></svg>
        www.brontlearn.co.uk.
      </li>
    </ul>
  </section>
</body>
</html>
```